Silver Bloom Marisol's Cleaning Service Business Cards Project

A business card with all contact details with logo design on there (already have a logo) eye catching Logo and contact info on one side, full logo on the back, must target upper class residential and corporate companies, fitness companies, still keep it on the feminine side of things , must look elegant

Target Market(s)

Upper class homes and corporate companies

Industry/Entity Type

Cleaning Service

Contact Information for Business Card

Name: Marisol Quenby
Position: Director
ABN: 31647209853
Email: marisolssilvercleaning@tidymail.example
Number: 0417906354

Font styles to use
Decorative

Colors

Designer to choose colors to be used in the design.

Requirements
Must have
• Available Sydney Wide, contact info and logo on one side, full logo on the back
Nice to have
• Professional appearance
Should not have
• Cheap advert looking stuff

```html
<!DOCTYPE html>
<html lang="en">
<head>
<meta charset="utf-8">
<title>Silver Bloom – Business Cards</title>
<link rel="stylesheet" href="https://fonts.googleapis.com/css2?family=Noto+Serif:wght@400;700&family=Nunito+Sans:wght@400;600&display=swap">
<style>
  :root {
    --canvas: #ececec;
    --card-white: #fbfbfb;
    --teal: #6eb5b8;
    --ink: #2e3442;
    --muted: #5d6270;
    --rule: #b9bcc2;
    --on-teal: #f4fbfb;
  }
  * { box-sizing: border-box; margin: 0; padding: 0; }
  html, body { width: 1200px; height: 1110px; overflow: hidden; }
  body {
    background: var(--canvas);
    font-family: "Nunito Sans", Arial, sans-serif;
    display: flex;
    flex-direction: column;
    align-items: center;
    justify-content: center;
    gap: 70px;
  }
  .card {
    width: 640px;
    height: 366px;
    border-radius: 3px;
    box-shadow: 0 10px 24px rgba(0,0,0,0.10), 0 2px 4px rgba(0,0,0,0.06);
    display: flex;
    flex-direction: column;
    align-items: center;
    justify-content: center;
    text-align: center;
  }
  .card--front { background: var(--card-white); color: var(--muted); }
  .card--back { background: var(--teal); color: var(--on-teal); }

  .holder-name {
    font-family: "Noto Serif", Georgia, serif;
    font-weight: 700;
    font-size: 30px;
    color: var(--ink);
    letter-spacing: 0.5px;
  }
  .holder-role { font-size: 16px; margin-top: 2px; }
  .divider { width: 30px; height: 1px; background: var(--rule); margin: 18px 0 16px; }
  .contact-list { list-style: none; font-size: 17px; line-height: 1.6; }
  .contact-list li { display: flex; align-items: center; justify-content: center; gap: 8px; }
  .contact-icon { width: 15px; height: 15px; fill: none; stroke: var(--teal); stroke-width: 1.8; }
  .label { color: var(--teal); font-weight: 600; }

  .brand-name {
    font-family: "Noto Serif", Georgia, serif;
    font-weight: 400;
    color: var(--on-teal);
    text-transform: uppercase;
  }
  .brand-name__main { display: block; font-size: 40px; letter-spacing: 3px; }
  .brand-name__sub { display: block; font-size: 13px; letter-spacing: 5px; margin-top: 8px; }
  .brand-mark { width: 14px; height: 14px; border: 1.5px solid var(--on-teal); border-radius: 50%; margin-bottom: 18px; }
</style>
</head>
<body>
  <section class="card card--front" aria-label="Business card front">
    <h1 class="holder-name">Marisol Quenby</h1>
    <p class="holder-role">Director</p>
    <div class="divider"></div>
    <ul class="contact-list">
      <li>
        <svg class="contact-icon" viewBox="0 0 16 16" aria-hidden="true"><path d="M4 1.5 L6.5 4.5 L5 6.5 Q6.5 9.5 9.5 11 L11.5 9.5 L14.5 12 L12.5 14.5 Q5 13 1.5 3.5 Z"/></svg>
        <span>0417906354</span>
      </li>
      <li>
        <svg class="contact-icon" viewBox="0 0 16 16" aria-hidden="true"><rect x="1.5" y="3.5" width="13" height="9"/><path d="M1.5 3.5 L8 9 L14.5 3.5"/></svg>
        <span>marisolssilvercleaning@tidymail.example</span>
      </li>
      <li><span class="label">ABN :</span><span>31647209853</span></li>
    </ul>
  </section>

  <section class="card card--back" aria-label="Business card back">
    <div class="brand-mark" aria-hidden="true"></div>
    <p class="brand-name">
      <span class="brand-name__main">Silver Bloom</span>
      <span class="brand-name__sub">Marisol's Cleaning Service</span>
    </p>
  </section>
</body>
</html>
```